Calvanto Group Real Estate Company business cards

New business card design, we are generally happy with the basic layout of the existing front of business card, (feel free to change) but require a head shot photo on the back side.

http://www.calvanto.com.au/

Attached logos, and existing business card

------------------------------

Target Market(s)

Real estate

Industry/Entity Type

Real Estate

Contact Information for Business Card

Standard size double sided

Font styles to use
Other font styles liked:
• Futura

Requirements
Must have
• Photo head shot on the back side
Nice to have
• yes
Should not have
• No

```html
<!DOCTYPE html>
<html lang="en">
<head>
<meta charset="utf-8">
<title>Calvanto Group – Business Cards</title>
<link rel="stylesheet" href="https://fonts.googleapis.com/css2?family=Jost:wght@400;500;600;700&display=swap">
<style>
  :root {
    --purple: #2e2260;
    --orange: #f08c1a;
    --white: #ffffff;
    --ink: #2e2260;
    --backdrop: #d9d9dc;
  }
  * { box-sizing: border-box; margin: 0; padding: 0; }
  html, body { width: 1200px; height: 900px; overflow: hidden; }
  body {
    background: var(--backdrop);
    font-family: "Jost", sans-serif;
    position: relative;
  }
  .card {
    position: absolute;
    width: 600px;
    height: 343px;
    border-radius: 18px;
    overflow: hidden;
    box-shadow: 0 10px 28px rgba(0,0,0,0.25);
  }
  .card-shape { position: absolute; inset: 0; }

  /* Front */
  .card-front { left: 110px; top: 100px; background: var(--purple); }
  .front-brand {
    position: absolute; left: 0; right: 0; top: 82px;
    text-align: center; color: var(--white);
    font-size: 82px; font-weight: 500; letter-spacing: -1px; line-height: 1;
  }
  .front-services {
    position: absolute; left: 0; right: 0; top: 190px;
    text-align: center; color: var(--white);
    font-size: 20px; font-weight: 600; letter-spacing: 2px;
  }
  .front-web {
    position: absolute; right: 70px; bottom: 28px;
    color: var(--ink); font-size: 19px; font-weight: 400;
  }
  .front-web strong { font-weight: 700; }

  /* Back */
  .card-back { left: 490px; top: 470px; background: var(--white); }
  .back-brand {
    position: absolute; left: 34px; top: 82px;
    color: var(--purple); font-size: 54px; font-weight: 500;
    letter-spacing: -1px; line-height: 1;
  }
  .headshot {
    position: absolute; left: 370px; top: 18px;
    width: 200px; height: 200px; border-radius: 50%;
    background: radial-gradient(circle at 50% 45%, #e6e6ea 0%, #d4d4da 60%, #f4f4f6 100%);
  }
  .person { position: absolute; left: 40px; top: 168px; color: var(--ink); }
  .person-name { font-size: 27px; font-weight: 700; letter-spacing: 0.5px; line-height: 1.05; }
  .person-role { font-size: 14px; font-weight: 500; color: var(--orange); letter-spacing: 0.5px; margin-top: 2px; }
  .person-abn { font-size: 15px; margin-top: 2px; }
  .person-abn span { color: var(--orange); }
  .contact-list { list-style: none; margin-top: 6px; }
  .contact-list li {
    display: flex; align-items: center; gap: 8px;
    font-size: 14px; line-height: 1.35;
  }
  .contact-list svg { width: 12px; height: 12px; flex: none; }
  .tagline {
    position: absolute; right: 40px; bottom: 34px;
    color: var(--white); font-size: 19px; font-weight: 400;
    transform: rotate(-9deg); transform-origin: right bottom;
  }
</style>
</head>
<body>

  <section class="card card-front" aria-label="Business card front">
    <svg class="card-shape" viewBox="0 0 600 343" preserveAspectRatio="none">
      <path d="M0 326 C200 312 420 258 600 200" fill="none" stroke="var(--orange)" stroke-width="5"/>
      <path d="M0 333 C200 320 420 266 600 208 L600 343 L0 343 Z" fill="var(--white)"/>
    </svg>
    <div class="front-brand">calvanto</div>
    <div class="front-services">Buy | Sell | Rent</div>
    <div class="front-web">www.<strong>calvanto.com</strong>.au</div>
  </section>

  <section class="card card-back" aria-label="Business card back">
    <svg class="card-shape" viewBox="0 0 600 343" preserveAspectRatio="none">
      <path d="M0 208 L16 208 Q24 208 24 216 L24 296 Q24 304 16 304 L0 304 Z" fill="var(--purple)"/>
      <path d="M90 343 C300 320 470 280 600 226" fill="none" stroke="var(--orange)" stroke-width="5"/>
      <path d="M96 343 C300 328 470 290 600 236 L600 343 Z" fill="var(--purple)"/>
    </svg>
    <div class="back-brand">calvanto</div>
    <div class="headshot" role="img" aria-label="Head shot photo of the director"></div>
    <div class="person">
      <div class="person-name">DANIEL TRAN</div>
      <div class="person-role">DIRECTOR</div>
      <div class="person-abn"><span>ABN:</span> 12 345 678 901</div>
      <ul class="contact-list">
        <li>
          <svg viewBox="0 0 12 12"><rect x="3" y="0.5" width="6" height="11" rx="1.2" fill="none" stroke="var(--orange)" stroke-width="1.4"/><circle cx="6" cy="9.5" r="0.8" fill="var(--orange)"/></svg>
          0412 555 018
        </li>
        <li>
          <svg viewBox="0 0 12 12"><rect x="0.7" y="2" width="10.6" height="8" rx="1" fill="none" stroke="var(--orange)" stroke-width="1.4"/><path d="M1 2.5 L6 6.5 L11 2.5" fill="none" stroke="var(--orange)" stroke-width="1.4"/></svg>
          daniel.tran@calvanto.com.au
        </li>
        <li>
          <svg viewBox="0 0 12 12"><circle cx="6" cy="6" r="5.2" fill="none" stroke="var(--orange)" stroke-width="1.3"/><ellipse cx="6" cy="6" rx="2.2" ry="5.2" fill="none" stroke="var(--orange)" stroke-width="1.1"/><path d="M0.8 6 H11.2" stroke="var(--orange)" stroke-width="1.1"/></svg>
          www.calvanto.com.au
        </li>
      </ul>
    </div>
    <div class="tagline">find your place with us</div>
  </section>

</body>
</html>
```